Manuka Honey company needs a Upmarket, Luxury Website!

New Zealand, Taranaki based Manuka Honey company Rimu Vale Honey is looking for a new website, we are looking for an upmarket, luxury, serious website design. We export the highest quality quality Manuka Honey, straight from the Taranaki region.

Main export markets are Asia & Europe, also New Zealand & Australia.

Looking to have a beautiful, upmarket, serious, luxurious & graphical experience with mobile optimization in mind. Like the use of product staging/mockups

You can use copy from other websites to build the site and we will change the copy after the design is finished.

***Please include 'Honey Product' mockups in website.

*Will add illustrator files in coming days***

Feel free to make website functional in Shopify, Wordpress or WIX

Target Market(s)

Asia, Europe (main markets) New Zealand, Australia (Submarkets)

Coding

Coded - Design and coding required

Number of Pages Required

4 page

Requirements
Must have
• Home, Shop, About Us, Contact Us

Homepage to include:

Our Products
Company Video (video under construction)
What is MGO/KPS
Newsletter Opt-in

***(Not in Order)***

Please include 'Honey Product' mockups in website.
*Will add illustrator files in coming days
Nice to have
• FAQ & Partnership Inquiries (hyperlink in footer)

```html
<!DOCTYPE html>
<html lang="en">
<head>
<meta charset="utf-8">
<title>Rimu Vale Honey Co.</title>
<link href="https://fonts.googleapis.com/css2?family=Lato:wght@300;400;700;900&family=Arimo:wght@400;700&display=swap" rel="stylesheet">
<style>
:root{
  --gold:#e0a30c;
  --blue:#1f7fb5;
  --teal:#2a9bbf;
  --ink:#2b2b2b;
  --text:#4a4a4a;
  --grey:#f0f0f0;
  --line:#b9b9b9;
  --black:#141414;
  --white:#ffffff;
}
*{margin:0;padding:0;box-sizing:border-box}
html,body{width:1200px;height:4154px;overflow:hidden;background:var(--white)}
body{position:relative;font-family:'Lato',sans-serif;color:var(--text)}
.abs{position:absolute}
.btn{position:absolute;display:flex;align-items:center;justify-content:center;background:var(--gold);color:var(--white);font:700 16px 'Lato',sans-serif;letter-spacing:.3px;text-transform:uppercase}
.section-title{position:absolute;left:0;width:1200px;text-align:center;font:300 56px 'Lato',sans-serif;color:var(--ink);letter-spacing:1px}
.section-intro{position:absolute;left:70px;width:1060px;text-align:center;font:400 17px/29px 'Lato',sans-serif;color:var(--text)}

/* nav */
.site-nav{position:absolute;left:0;top:0;width:1200px;height:102px;background:var(--white);z-index:5}
.site-nav a{position:absolute;top:46px;font:700 14px 'Lato',sans-serif;color:var(--ink);text-decoration:none;text-transform:uppercase}
.site-nav a.active{color:var(--teal)}
.brand-badge{position:absolute;border-radius:50%;background:var(--white);border:3px solid #555;display:flex;align-items:center;justify-content:center;text-align:center;font:700 15px/19px 'Lato',sans-serif;color:#333;text-transform:uppercase}

/* hero */
.hero{position:absolute;left:0;top:102px;width:1200px;height:732px;clip-path:polygon(0 0,100% 0,100% 100%,0 89.2%);background:linear-gradient(180deg,#3f6a22 0%,#5f8e2e 35%,#6c8a3a 55%,#5a4a38 70%,#4a3a2c 100%)}
.hero-title{position:absolute;left:77px;top:214px;font:900 66px/74px 'Lato',sans-serif;color:var(--white);text-transform:uppercase;letter-spacing:-.5px}
.hero-product{position:absolute;left:694px;top:300px;width:380px;height:421px;border-radius:18px;background:linear-gradient(180deg,#cdb27a 0%,#23343a 25%,#1c2c30 70%,#8a3a1c 100%)}

/* product cards */
.card{position:absolute;top:1077px;width:329px;height:407px;border:1px solid var(--line);background:var(--white)}
.card::after{content:"";position:absolute;inset:7px;border:1px solid var(--line)}
.card-jar{position:absolute;left:100px;top:38px;width:128px;height:228px;border-radius:14px;background:linear-gradient(180deg,#d2b782 0%,#1f3236 24%,#1b2a2e 75%,#8c3c1c 100%)}
.quick-view{position:absolute;left:90px;top:178px;width:150px;height:50px;background:rgba(20,20,20,.88);color:var(--white);font:700 16px 'Lato',sans-serif;display:flex;align-items:center;justify-content:center;text-transform:uppercase}
.card h3{position:absolute;left:0;top:292px;width:100%;text-align:center;font:700 18px 'Lato',sans-serif;color:var(--blue);text-transform:uppercase}
.card p{position:absolute;left:20px;right:20px;top:322px;text-align:center;font:400 16px/29px 'Lato',sans-serif;color:var(--text)}

.bee{position:absolute;width:72px;height:64px;border-radius:40%;background:#f4e6b6}

/* about */
.feature-box{position:absolute;border:2px solid var(--gold)}
.feature-title{position:absolute;font:300 58px/56px 'Lato',sans-serif;color:var(--ink);text-transform:uppercase}
.feature-text{position:absolute;font:400 17px/29px 'Lato',sans-serif;color:var(--text)}

/* video */
.video{position:absolute;left:166px;top:2436px;width:870px;height:406px;border:4px solid var(--white);box-shadow:0 2px 8px rgba(0,0,0,.35);background:linear-gradient(135deg,#4b5a2e 0%,#7a6a3a 40%,#a8742e 65%,#3a3a28 100%)}
.play{position:absolute;left:391px;top:160px}

/* table */
.mgo-table{position:absolute;left:45px;top:3121px;width:436px;border:3px solid var(--white);background:var(--white);font-family:'Arimo',sans-serif}
.mgo-table table{width:100%;border-collapse:collapse}
.mgo-table th,.mgo-table td{border:2px solid #222;text-align:center;height:51px;font-size:17px;color:#111}
.mgo-table th{font-weight:700;height:60px}
.hex{display:inline-block;width:38px;height:38px;clip-path:polygon(50% 0,100% 25%,100% 75%,50% 100%,0 75%,0 25%);color:var(--white);font:700 12px/38px 'Arimo',sans-serif}
.mgo-note{font:400 11px 'Arimo',sans-serif;color:#111;padding:4px 6px;border:2px solid #222;border-top:none}

/* newsletter */
.newsletter{position:absolute;left:76px;top:3624px;width:1048px;height:215px;border:1px solid var(--line);background:var(--white)}
.email{position:absolute;left:518px;top:3708px;width:406px;height:49px;background:var(--grey);border:1px solid #aaa;font:700 15px 'Lato',sans-serif;color:#333;padding-left:18px;display:flex;align-items:center}

/* footer */
.site-footer{position:absolute;left:0;top:3928px;width:1200px;height:226px;background:var(--black)}
.site-footer nav a{position:absolute;top:96px;transform:translateX(-50%);font:700 15px 'Lato',sans-serif;color:var(--white);text-decoration:none;text-transform:uppercase;white-space:nowrap}
.copyright{position:absolute;left:0;top:124px;width:1200px;text-align:center;font:400 13px 'Lato',sans-serif;color:#ddd}
.social{position:absolute;top:159px;width:18px;height:18px;border-radius:50%;background:var(--white)}
</style>
</head>
<body>

<header class="site-nav">
  <a class="active" href="#" style="left:81px">Home</a>
  <a href="#" style="left:179px">About Company</a>
  <a href="#" style="left:364px">Products</a>
  <a href="#" style="left:768px">What is MGO/KPS</a>
  <a href="#" style="left:961px">Contact Us</a>
</header>
<div class="brand-badge" style="left:518px;top:18px;width:164px;height:164px;z-index:6">Rimu Vale<br>Honey Co</div>

<section class="hero" role="img" aria-label="Forest of tall trees behind a wooden deck"></section>
<div class="hero-product" role="img" aria-label="Two jars of active manuka honey"></div>
<h1 class="hero-title">Welcome to<br>Rimu Vale Honey Co.</h1>
<a class="btn" style="left:76px;top:489px;width:221px;height:48px">View all products</a>

<h2 class="section-title" style="top:888px">Our Products</h2>
<p class="section-intro" style="top:972px">Sed ut perspiciatis unde omnis iste natus error sit voluptatem accusantium doloremque laudantium, totam rem aperiam, eaque ipsa quae ab illo inventore veritatis et quasi architecto beatae vitae dicta sunt explicabo</p>

<article class="card" style="left:76px">
  <div class="card-jar" role="img" aria-label="Manuka honey jar"></div>
  <div class="quick-view">Quick view</div>
  <h3>Product Heading</h3>
  <p>Sed ut perspiciatis unde omnis iste natus error sit voluptatem</p>
</article>
<article class="card" style="left:437px">
  <div class="card-jar" role="img" aria-label="Manuka honey jar"></div>
  <h3>Product Heading</h3>
  <p>Sed ut perspiciatis unde omnis iste natus error sit voluptatem</p>
</article>
<article class="card" style="left:795px">
  <div class="card-jar" role="img" aria-label="Manuka honey jar"></div>
  <h3>Product Heading</h3>
  <p>Sed ut perspiciatis unde omnis iste natus error sit voluptatem</p>
</article>

<a class="btn" style="left:489px;top:1529px;width:222px;height:48px">View all products</a>
<div class="bee" style="left:14px;top:1515px" role="img" aria-label="Cartoon bee with dashed flight path"></div>
<div class="bee" style="left:1000px;top:1510px" role="img" aria-label="Cartoon bee with dashed flight path"></div>

<!-- about -->
<svg class="abs" style="left:0;top:1620px" width="1200" height="610" viewBox="0 1620 1200 610">
  <polygon points="0,1707 640,1690 640,2150 0,2137" fill="#f0f0f0"/>
  <defs><linearGradient id="hive" x1="0" y1="0" x2="1" y2="1"><stop offset="0" stop-color="#8fb35a"/><stop offset=".45" stop-color="#c9a05a"/><stop offset="1" stop-color="#6a4a26"/></linearGradient></defs>
  <polygon points="616,1648 1200,1629 1200,2218 616,2186" fill="url(#hive)" role="img" aria-label="Beekeeper lifting a honeycomb frame from a hive"/>
</svg>
<div class="feature-box" style="left:76px;top:1739px;width:627px;height:366px"></div>
<h2 class="feature-title" style="left:105px;top:1770px">About<br>Rimu Vale Honey</h2>
<p class="feature-text" style="left:105px;top:1893px;width:470px">Sed ut perspiciatis unde omnis iste natus error sit voluptatem accusantium doloremque laudantium, totam rem aperiam, eaque ipsa quae ab illo inventore veritatis et quasi architecto beatae vitae dicta sunt explicabo.</p>
<a class="btn" style="left:105px;top:2021px;width:137px;height:49px">Read more</a>
<div class="brand-badge" style="left:634px;top:1853px;width:136px;height:136px;font-size:13px;line-height:17px">Rimu Vale<br>Honey Co</div>

<!-- story -->
<h2 class="section-title" style="top:2254px">Our Story</h2>
<p class="section-intro" style="top:2338px">Sed ut perspiciatis unde omnis iste natus error sit voluptatem accusantium doloremque laudantium, totam rem aperiam, eaque ipsa quae ab illo inventore veritatis et quasi architecto beatae vitae dicta sunt explicabo</p>
<div class="video" role="img" aria-label="Beekeepers in protective suits tending wooden hives">
  <svg class="play" width="84" height="84" viewBox="0 0 84 84"><circle cx="42" cy="42" r="38" fill="#fff"/><circle cx="42" cy="42" r="31" fill="#222"/><polygon points="34,26 60,42 34,58" fill="#fff"/></svg>
</div>
<a class="btn" style="left:489px;top:2866px;width:222px;height:49px">Watch video</a>
<div class="bee" style="left:20px;top:2540px" role="img" aria-label="Cartoon bee with dashed flight path"></div>
<div class="bee" style="left:1095px;top:2628px" role="img" aria-label="Cartoon bee with dashed flight path"></div>

<!-- mgo -->
<svg class="abs" style="left:0;top:2970px" width="1200" height="600" viewBox="0 2970 1200 600">
  <polygon points="0,3015 1200,3057 1200,3516 0,3530" fill="#f0f0f0"/>
  <defs><linearGradient id="honey" x1="0" y1="0" x2="1" y2="1"><stop offset="0" stop-color="#3a2a18"/><stop offset=".5" stop-color="#5a3a16"/><stop offset="1" stop-color="#1e1710"/></linearGradient></defs>
  <polygon points="0,2976 584,3014 584,3540 0,3565" fill="url(#honey)" role="img" aria-label="Honey dripping from a wooden dipper"/>
</svg>
<div class="mgo-table">
  <table>
    <tr><th style="width:29%">STRENGTH</th><th>MGO (antibacterial)*</th><th style="width:22%">KPS**</th></tr>
    <tr><td>MILD</td><td><span class="hex" style="background:#2f9a45">120+</span></td><td>10-12</td></tr>
    <tr><td>MEDIUM</td><td><span class="hex" style="background:#e0742a">220+</span></td><td>13-15</td></tr>
    <tr><td>HIGH</td><td><span class="hex" style="background:#c8202a">400+</span></td><td>18-20</td></tr>
    <tr><td>ULTRA-HIGH</td><td><span class="hex" style="background:#5a2a7a">900+</span></td><td>32-35</td></tr>
  </table>
  <div class="mgo-note">Note: Approximate measurement shown to the nearest value.</div>
</div>
<div class="feature-box" style="left:497px;top:3086px;width:627px;height:367px"></div>
<h2 class="feature-title" style="left:600px;width:484px;top:3124px;text-align:right">What is<br>MGO/KPS</h2>
<p class="feature-text" style="left:600px;width:482px;top:3241px;text-align:right">Sed ut perspiciatis unde omnis iste natus error sit voluptatem accusantium doloremque laudantium, totam rem aperiam, eaque ipsa quae ab illo inventore veritatis et quasi architecto beatae vitae dicta sunt explicabo.</p>
<a class="btn" style="left:945px;top:3370px;width:137px;height:46px">Read more</a>

<!-- newsletter -->
<div class="newsletter"></div>
<h2 class="feature-title" style="left:113px;top:3680px">Newsletter<br>Sign up</h2>
<div class="email">EMAIL ADDRESS</div>
<a class="btn" style="left:935px;top:3708px;width:160px;height:49px">Subscribe</a>
<div class="bee" style="left:816px;top:3545px" role="img" aria-label="Cartoon bee with dashed flight path"></div>
<div class="bee" style="left:1115px;top:3538px" role="img" aria-label="Cartoon bee with dashed flight path"></div>
<div class="bee" style="left:46px;top:3840px" role="img" aria-label="Cartoon bee with dashed flight path"></div>
<div class="bee" style="left:346px;top:3828px" role="img" aria-label="Cartoon bee with dashed flight path"></div>

<footer class="site-footer">
  <nav>
    <a href="#" style="left:113px">Home</a>
    <a href="#" style="left:255px">About Company</a>
    <a href="#" style="left:415px">Products</a>
    <a href="#" style="left:577px">What is MGO/KPS</a>
    <a href="#" style="left:716px">FAQ</a>
    <a href="#" style="left:874px">Partnership Inquiries</a>
    <a href="#" style="left:1065px">Contact Us</a>
  </nav>
  <p class="copyright">Copyright © 2021. Company Name. All Right Reserved</p>
  <span class="social" style="left:497px"></span>
  <span class="social" style="left:543px"></span>
  <span class="social" style="left:590px"></span>
  <span class="social" style="left:639px"></span>
  <span class="social" style="left:688px"></span>
</footer>
<div class="brand-badge" style="left:545px;top:3881px;width:110px;height:110px;font-size:11px;line-height:14px;z-index:6">Rimu Vale<br>Honey Co</div>

</body>
</html>
```